Equipment Finance Specialist I work with companies who need the funds to buy their equipment

I would like a business card that stands out on the shelves. I want to be able to hand it to someone and say WOW. This card should have my logo.
You can put color into it I am very open on design and color

What my company does is we deal with dealerships that sell equipment such as Dump Trucks garbage trucks tractors trailers. Customers get referred to us and depending on their time in business we will ask for the following items

Companies that have been in business for more than two years we have a credit application program up to 250K . With this program we need the following items Credit application filled out(which is what I would like to be able for the customer to click on my website to get.) as well as three current month bank statements.

Deals over 250k we will need the following items

2 years business tax returns
2 years personal tax returns
Profit & Loss statement
Personal Financial Statement

what we do
100% FINANCING
SEASONAL PAYMENTS
LOAN BALLOON PAYMENTS
TRAC LEASING
LOW-INTEREST REFINANCING RATES
DEBT CONSOLIDATION

We specialize in creative financing solutions and offer a variety of reliable, flexible and expandable lending choices.

Target Market(s)

Trucking Companies

Industry/Entity Type

Trucking Company

Contact Information for Business Card

* $250,000 Application only Program
* Loans from $30,000 to 5,000,000
* Competitive Interest Rates

Font styles to use
Serif
Sans Serif

Colors

Designer to choose colors to be used in the design.

Requirements
Must have
• On the back of the card.
• * $250,000 Application only Program
• * Loans from $30,000 to 5,000,000
• My name, email, website. address
• * Competitive Interest Rates
• * 100% Financing
Nice to have
• I want my logo to pop on the card
• My logo is the great one I would like to use
Should not have
• I am up for your creativity as well

```html
<!DOCTYPE html>
<html lang="en">
<head>
<meta charset="utf-8">
<title>Summit Capital – Business Card</title>
<link href="https://fonts.googleapis.com/css2?family=Open+Sans:wght@400;700&display=swap" rel="stylesheet">
<style>
  :root {
    --navy: #1b2f6e;
    --red: #d3183a;
    --ink: #555a60;
    --paper: #ffffff;
    --stage: #2a2a2c;
  }
  * { margin: 0; padding: 0; box-sizing: border-box; }
  html, body { width: 1200px; height: 892px; overflow: hidden; }
  body {
    background: var(--stage);
    font-family: "Open Sans", Arial, sans-serif;
    position: relative;
  }
  .card {
    position: absolute;
    width: 620px;
    height: 354px;
    background: var(--paper);
    box-shadow: 0 10px 30px rgba(0,0,0,.45);
  }
  .card--front { left: 80px; top: 70px; }
  .card--back { left: 500px; top: 468px; }

  /* front */
  .brand-mark {
    display: flex; align-items: center; gap: 12px;
  }
  .brand-mark__dot {
    width: 44px; height: 44px; border-radius: 50%; background: var(--navy);
  }
  .brand-mark__name {
    font-weight: 700; color: var(--navy); font-size: 30px; letter-spacing: .5px;
  }
  .card--front .brand-mark {
    position: absolute; top: 96px; left: 0; right: 0; justify-content: center;
  }
  .offer {
    position: absolute; left: 0; right: 0; top: 220px;
    text-align: center; color: var(--ink); font-size: 15px; line-height: 1.45;
  }
  .offer .sep { color: var(--navy); margin: 0 4px; }

  /* back */
  .card--back .brand-mark {
    position: absolute; top: 40px; right: 40px;
  }
  .card--back .brand-mark__dot { width: 36px; height: 36px; }
  .card--back .brand-mark__name { font-size: 24px; }
  .rule {
    position: absolute; left: 34px; right: 34px; height: 2px; background: var(--navy);
  }
  .rule--top { top: 130px; left: 260px; }
  .rule--bottom { top: 298px; }
  .person { position: absolute; left: 34px; top: 150px; }
  .person__name { color: var(--navy); font-weight: 700; font-size: 20px; line-height: 1.1; }
  .person__title { color: var(--red); font-size: 14px; letter-spacing: .5px; }
  .contacts {
    position: absolute; left: 34px; top: 212px; list-style: none;
    color: var(--ink); font-size: 14px; line-height: 26px;
  }
  .contacts li, .address { display: flex; align-items: center; gap: 10px; }
  .contacts svg, .address svg { width: 14px; height: 14px; fill: var(--navy); flex: none; }
  .address {
    position: absolute; left: 34px; top: 310px; color: var(--ink); font-size: 14px;
  }
</style>
</head>
<body>

<section class="card card--front">
  <div class="brand-mark">
    <span class="brand-mark__dot"></span>
    <span class="brand-mark__name">SUMMIT CAPITAL</span>
  </div>
  <p class="offer">
    $250,000 Application only Program<span class="sep">●</span>Loans from $30,000 to 5,000,000<br>
    Competitive Interest Rates<span class="sep">●</span>100% Financing
  </p>
</section>

<section class="card card--back">
  <div class="brand-mark">
    <span class="brand-mark__dot"></span>
    <span class="brand-mark__name">SUMMIT CAPITAL</span>
  </div>
  <div class="rule rule--top"></div>

  <div class="person">
    <p class="person__name">MARK ELLISON</p>
    <p class="person__title">PRESIDENT</p>
  </div>

  <ul class="contacts">
    <li>
      <svg viewBox="0 0 24 24" aria-hidden="true"><path d="M6.6 10.8a15 15 0 0 0 6.6 6.6l2.2-2.2a1 1 0 0 1 1-.25 11.4 11.4 0 0 0 3.6.57 1 1 0 0 1 1 1V20a1 1 0 0 1-1 1A17 17 0 0 1 3 4a1 1 0 0 1 1-1h3.5a1 1 0 0 1 1 1c0 1.25.2 2.45.57 3.6a1 1 0 0 1-.25 1z"/></svg>
      555 0142 7788
    </li>
    <li>
      <svg viewBox="0 0 24 24" aria-hidden="true"><path d="M2 5h20v14H2zm2 2v.5l8 5 8-5V7l-8 5z"/></svg>
      mark@summitcapital.com
    </li>
    <li>
      <svg viewBox="0 0 24 24" aria-hidden="true"><circle cx="12" cy="12" r="10"/></svg>
      www.summitcapital.com
    </li>
  </ul>

  <div class="rule rule--bottom"></div>
  <p class="address">
    <svg viewBox="0 0 24 24" aria-hidden="true"><path d="M12 2a7 7 0 0 0-7 7c0 5 7 13 7 13s7-8 7-13a7 7 0 0 0-7-7zm0 9.5A2.5 2.5 0 1 1 12 6.5a2.5 2.5 0 0 1 0 5z"/></svg>
    1420 Harbor Lane Cedar Grove, NY 11020
  </p>
</section>

</body>
</html>
```